Holistic/ Sports Psychologist needs flyer design

I need a flyer designed that catches the attention of potential customers - (parents of young athletes and athletes) who may be looking for psychological services. I have a logo and all the relevant info for the flyer but would like someone to take it and make it look creative, fun, fresh and attention getting for high school and college athletes. The colors used can be from my logo design which represents my holistic approach.
Target Market(s)
high school and collegiate athletes
Industry/Entity Type
sports psychology
Requirements
Must have
- Info I put on the flyer with my logo and please add some graphics and color based on my logo

```html
<!DOCTYPE html>
<html lang="en">
<head>
<meta charset="utf-8">
<title>Holistic Psychology and Sports Psychology Consulting</title>
<link href="https://fonts.googleapis.com/css2?family=Itim&family=Exo+2:wght@500&family=Poppins:wght@400;600;700&display=swap" rel="stylesheet">
<style>
  :root{
    --blue:#2f5f98;
    --blue-dark:#27508a;
    --green:#8cc965;
    --green-soft:#86b784;
    --teal:#6fa398;
    --ink:#1c1c1c;
    --white:#ffffff;
  }
  *{margin:0;padding:0;box-sizing:border-box}
  html,body{width:1035px;height:1200px;overflow:hidden;background:#fff}
  .flyer{position:relative;width:1035px;height:1200px;background:var(--white);overflow:hidden;font-family:"Poppins",sans-serif;color:var(--ink)}
  .backdrop{position:absolute;inset:0}
  .brand{position:absolute;left:62px;top:47px;display:flex;align-items:center}
  .brand-mark{width:112px;height:112px;border-radius:50%;border:4px solid var(--blue);background:linear-gradient(160deg,#e8f1fa,#8cc965);}
  .brand-name{position:absolute;left:120px;top:22px;font-family:"Itim",cursive;font-size:29px;color:var(--blue);letter-spacing:1px;white-space:nowrap}
  .brand-bar{position:absolute;left:113px;top:64px;width:357px;height:22px;background:var(--green)}
  .headline{position:absolute;left:60px;top:168px;font-family:"Itim",cursive;color:var(--blue);font-size:49px;line-height:54px}
  .headline .accent{display:block;color:var(--green);font-size:108px;line-height:100px;margin-top:-4px}
  .ways{position:absolute;left:62px;top:446px;font-family:"Exo 2",sans-serif;font-size:18.5px;letter-spacing:2px;line-height:23px}
  .ways .l1{color:var(--blue)} .ways .l2{color:var(--green)}
  .service{position:absolute;left:62px;width:520px}
  .service .icon{position:absolute;left:0;top:0;width:70px;height:70px}
  .service h3{position:absolute;left:90px;top:-8px;font-family:"Exo 2",sans-serif;font-weight:500;font-size:17.5px;letter-spacing:2px;color:var(--blue);white-space:nowrap}
  .service p{position:absolute;left:90px;top:17px;width:410px;font-size:13.7px;line-height:16.5px}
  .bio{position:absolute;left:646px;top:581px;width:328px;height:413px;border-radius:26px;background:linear-gradient(180deg,var(--green-soft) 0%,#6d9e94 45%,var(--blue) 100%);color:var(--white);padding:114px 22px 0 24px;font-size:14.2px;line-height:16.4px}
  .bio h4{font-weight:700;font-size:16.5px;line-height:19px}
  .bio .spec{font-weight:600;margin-top:17px}
  .portrait{position:absolute;left:697px;top:457px;width:230px;height:230px;border-radius:50%;border:6px solid var(--white);background:radial-gradient(circle at 50% 40%,#b79a86,#4b3a35 55%,#3a4f6a 100%)}
  .telehealth{position:absolute;left:225px;top:1015px;width:584px;height:66px;border-radius:6px;background:var(--blue);text-align:center;padding-top:6px}
  .telehealth .t1{color:var(--white);font-weight:700;font-size:22.5px;line-height:28px}
  .telehealth .t2{color:var(--green);font-size:21.5px;line-height:26px}
  .contact{position:absolute;top:1115px;color:var(--white);display:flex;align-items:center;gap:8px}
  .contact svg{width:16px;height:16px;flex:none}
  .contact .txt{font-size:20px;line-height:19px}
  .contact.phone .txt{font-weight:700;font-size:23px}
</style>
</head>
<body>
<div class="flyer">
  <svg class="backdrop" width="1035" height="1200" viewBox="0 0 1035 1200">
    <defs>
      <linearGradient id="footerFill" x1="0" y1="0" x2="0" y2="1">
        <stop offset="0" stop-color="#86b784"/>
        <stop offset="1" stop-color="#6fa398"/>
      </linearGradient>
      <linearGradient id="fieldFill" x1="0" y1="0" x2="1" y2="1">
        <stop offset="0" stop-color="#5c9a32"/>
        <stop offset="1" stop-color="#3d7a22"/>
      </linearGradient>
    </defs>
    <path class="swoosh" d="M0 362 Q330 490 700 372 Q360 455 0 385 Z" fill="var(--blue)"/>
    <path class="photo-ring" d="M835 10 A218 218 0 0 0 720 395" fill="none" stroke="var(--green)" stroke-width="9"/>
    <circle cx="842" cy="220" r="214" fill="url(#fieldFill)" role="img" aria-label="Photo of sports balls, rackets and running shoes on green grass"/>
    <path class="footer-band" d="M0 1122 Q517 1040 1035 1122 L1035 1200 L0 1200 Z" fill="url(#footerFill)"/>
  </svg>

  <div class="brand">
    <div class="brand-mark"></div>
    <div class="brand-bar"></div>
    <div class="brand-name">Dr. Elena Brightwater</div>
  </div>

  <h1 class="headline">Holistic Psychology and<br>Sports Psychology<span class="accent">Consulting</span></h1>

  <div class="ways">
    <div class="l1">WAYS TO IMPROVE ATHLETIC PERFORMANCE</div>
    <div class="l2">USING SPORTS AND HOLISTIC PSYCHOLOGY</div>
  </div>

  <div class="service" style="top:510px">
    <svg class="icon" viewBox="0 0 70 70"><circle cx="35" cy="35" r="33" fill="none" stroke="var(--blue)" stroke-width="2"/><circle cx="37" cy="24" r="9" fill="none" stroke="var(--green)" stroke-width="3"/><path d="M16 44 h20 l10 -5 v6 l-14 7 h-16z" fill="var(--blue)"/></svg>
    <h3>Mental Skills Training</h3>
    <p>Ex visualization, goal-setting, motivation,<br>self- talk, mindset, concentration techniques</p>
  </div>

  <div class="service" style="top:599px">
    <svg class="icon" viewBox="0 0 70 70"><circle cx="35" cy="35" r="33" fill="none" stroke="var(--blue)" stroke-width="2"/><g fill="var(--blue)"><rect x="18" y="38" width="6" height="14"/><rect x="27" y="32" width="6" height="20"/><rect x="36" y="26" width="6" height="26"/><rect x="45" y="20" width="6" height="32"/></g><path d="M20 30 l26 -16" stroke="var(--green)" stroke-width="3"/></svg>
    <h3>Performance Enhancement</h3>
    <p>eliminate psychological barriers that are hindering performance such as self- doubt, perfectionism, fear of failure, and burnout</p>
  </div>

  <div class="service" style="top:697px">
    <svg class="icon" viewBox="0 0 70 70"><circle cx="35" cy="35" r="33" fill="none" stroke="var(--blue)" stroke-width="2"/><path d="M24 52 v-10 l-4 -2 4 -6 c0 -10 8 -14 16 -12 c7 2 10 8 9 14 l-4 6 v10z" fill="var(--blue)"/><path d="M36 24 c-6 -2 -8 -8 -6 -12 c5 1 7 6 6 12 c1 -6 5 -9 10 -9 c0 5 -4 9 -10 9" fill="var(--green)"/></svg>
    <h3>Mental Health</h3>
    <p>anxiety and stress management by using relaxation techniques, breathwork, and mindfulness practices</p>
  </div>

  <div class="service" style="top:787px">
    <svg class="icon" viewBox="0 0 70 70"><circle cx="35" cy="35" r="33" fill="none" stroke="var(--blue)" stroke-width="2"/><circle cx="30" cy="18" r="4" fill="var(--green)"/><rect x="42" y="16" width="9" height="14" rx="2" fill="var(--green)"/><path d="M14 44 h20 l12 -6 v6 l-16 8 h-16z" fill="var(--blue)"/></svg>
    <h3>Injury Recovery Support</h3>
    <p>assist athletes in maintaining resilience &amp; positive mental attitude during rehabilitation as well as processing emotions relating to any potential trauma caused by the injury or life transitions resulting from it.</p>
  </div>

  <div class="service" style="top:913px">
    <svg class="icon" viewBox="0 0 70 70"><circle cx="35" cy="35" r="33" fill="none" stroke="var(--blue)" stroke-width="2"/><circle cx="35" cy="24" r="5" fill="var(--blue)"/><path d="M18 34 l10 4 h14 l10 -4 M24 50 q11 -8 22 0" stroke="var(--blue)" stroke-width="4" fill="none"/><circle cx="20" cy="18" r="3" fill="var(--green)"/><circle cx="50" cy="18" r="3" fill="var(--green)"/></svg>
    <h3>Burnout prevention</h3>
    <p>teach athletes how to have balance in sports and life so they can experience longevity in their sports as well as overall optimal health and well-being.</p>
  </div>

  <div class="bio">
    <h4>Dr. Elena Brightwater</h4>
    <div>is a licensed psychologist. She understands the unique experiences of athletes due to her background as an All-American swimmer, collegiate and age group swim coach, parent of a collegiate/professional athlete, and sports psychology researcher. She works with athletes to optimize performance and overall well-being.</div>
    <div class="spec">Her specializations include:</div>
    <div>performance anxiety, mental performance, stress management, anxiety, depressions, trauma, life transitions, relationship issues, injury, and sleep</div>
  </div>
  <div class="portrait" role="img" aria-label="Portrait photo of the psychologist"></div>

  <div class="telehealth">
    <div class="t1">All services are provided online via telehealth</div>
    <div class="t2">Sessions are 30 or 55 minutes.</div>
  </div>

  <div class="contact" style="left:62px">
    <svg viewBox="0 0 16 16"><path d="M8 1 a5 5 0 0 1 5 5 c0 4 -5 9 -5 9 s-5 -5 -5 -9 a5 5 0 0 1 5 -5z" fill="var(--blue)"/><circle cx="8" cy="6" r="2" fill="#fff"/></svg>
    <div class="txt">2280 Harbor Lane #105<br>Coral Bay, FL 32099</div>
  </div>
  <div class="contact phone" style="left:425px">
    <svg viewBox="0 0 16 16"><circle cx="8" cy="8" r="7.5" fill="var(--blue)"/><path d="M5 4 l2 2 -1 1 q1 2 3 3 l1 -1 2 2 -1 1.5 q-4 0 -7 -6z" fill="#fff"/></svg>
    <div class="txt">555-013-2470</div>
  </div>
  <div class="contact" style="left:673px">
    <svg viewBox="0 0 16 16"><circle cx="8" cy="8" r="7" fill="none" stroke="var(--blue)" stroke-width="1.5"/><path d="M1 8 h14 M8 1 q-4 7 0 14 q4 -7 0 -14" fill="none" stroke="var(--blue)" stroke-width="1.2"/></svg>
    <div class="txt">www.drelenabrightwater.com</div>
  </div>
</div>
</body>
</html>
```